Business Card for Vorla Parts Wholesale supplier

Hi There! I need a new business card for our company. We are specialized in selling Vorla parts, mostly we sell new LCD screens for Zelnar and Drelks. I would like to see that back in the design.

You can find the colors and logo's on our website: www.hartuvo.nl

Industry/Entity Type

Business

Contact Information for Business Card

My Details:
Tobias Lindqvist

Phone: 0031687203316
E-mail: Tobias@hartuvo.nl

Slogan: "Because Quality Matters"

Font styles to use
Sans Serif

Colors

Designer to choose colors to be used in the design.

Requirements
Must have
• A Black backside with the Hartuvo logo on it. The front side should be clean with only my contact details.
• But I'm also open for something really different or awesome!
Nice to have
• Remember that we are in the parts & repairing industry, So i'll be handing those business cards mainly to repair companies. Maybe you can do something with that thought :)

```html
<!DOCTYPE html>
<html lang="en">
<head>
<meta charset="utf-8">
<title>Hartuvo Business Card</title>
<link href="https://fonts.googleapis.com/css2?family=Exo+2:wght@300;400;600&family=Open+Sans:wght@600&display=swap" rel="stylesheet">
<style>
  :root {
    --brand-orange: #f37021;
    --ink-black: #111111;
    --text-grey: #444444;
    --rule-grey: #9a9a9a;
    --paper-white: #ffffff;
    --backdrop: #6a4b35;
    --faint-orange: #fdf0e6;
  }
  * { margin: 0; padding: 0; box-sizing: border-box; }
  html, body { width: 1200px; height: 987px; overflow: hidden; }
  body { background: var(--backdrop); position: relative; font-family: "Exo 2", sans-serif; }

  .card {
    position: absolute;
    left: 293px;
    width: 615px;
    height: 350px;
    overflow: hidden;
    box-shadow: 0 4px 12px rgba(0,0,0,0.35);
  }
  .card-front { top: 130px; background: var(--paper-white); }
  .card-back { top: 506px; background: var(--brand-orange); }

  .front-decoration {
    position: absolute;
    left: -70px; top: 0;
    width: 340px; height: 340px;
    border-radius: 50%;
    background: var(--faint-orange);
  }

  .wordmark {
    position: absolute;
    display: flex;
    align-items: center;
    gap: 12px;
    font-family: "Exo 2", sans-serif;
    font-weight: 600;
    letter-spacing: 0.5px;
  }
  .wordmark-dot { border-radius: 50%; flex: none; }

  .front-wordmark { left: 313px; top: 53px; font-size: 50px; line-height: 50px; color: var(--ink-black); }
  .front-wordmark .wordmark-dot { width: 46px; height: 46px; background: var(--brand-orange); }

  .holder-name {
    position: absolute;
    left: 45px; top: 208px;
    font-size: 23px;
    font-weight: 600;
    color: var(--brand-orange);
    letter-spacing: 0.3px;
  }
  .name-rule {
    position: absolute;
    left: 45px; top: 245px;
    width: 525px; height: 1px;
    background: var(--rule-grey);
  }
  .contact-list { position: absolute; left: 45px; top: 258px; list-style: none; }
  .contact-item {
    display: flex; align-items: center; gap: 7px;
    height: 25px;
    font-size: 16px; font-weight: 300;
    color: var(--text-grey);
  }
  .contact-icon { width: 15px; height: 15px; flex: none; }

  .card-bands { position: absolute; left: 0; top: 0; }
  .web-address {
    position: absolute;
    right: 45px; top: 326px;
    font-size: 15px; font-weight: 300;
    letter-spacing: 3.4px;
    color: var(--paper-white);
  }

  .back-wordmark { left: 0; right: 0; top: 151px; justify-content: center; font-size: 62px; line-height: 62px; color: var(--paper-white); }
  .back-wordmark .wordmark-dot { width: 56px; height: 56px; background: var(--paper-white); }
  .slogan {
    position: absolute;
    left: 0; right: 0; top: 280px;
    text-align: center;
    font-family: "Open Sans", sans-serif;
    font-weight: 600;
    font-size: 19px;
    color: var(--paper-white);
  }
</style>
</head>
<body>
  <section class="card card-front" aria-label="Business card front">
    <div class="front-decoration" aria-hidden="true"></div>

    <div class="wordmark front-wordmark">
      <span class="wordmark-dot" aria-hidden="true"></span>
      <span class="wordmark-name">hartuvo</span>
    </div>

    <h1 class="holder-name">Tobias Lindqvist</h1>
    <div class="name-rule"></div>

    <ul class="contact-list">
      <li class="contact-item">
        <svg class="contact-icon" viewBox="0 0 24 24" aria-hidden="true">
          <path fill="#f37021" d="M6.6 10.8c1.4 2.8 3.8 5.1 6.6 6.6l2.2-2.2c.3-.3.7-.4 1-.2 1.1.4 2.3.6 3.6.6.6 0 1 .4 1 1V20c0 .6-.4 1-1 1C10.6 21 3 13.4 3 4c0-.6.4-1 1-1h3.5c.6 0 1 .4 1 1 0 1.3.2 2.5.6 3.6.1.3 0 .7-.2 1l-2.3 2.2z"/>
        </svg>
        <span>0031687203316</span>
      </li>
      <li class="contact-item">
        <svg class="contact-icon" viewBox="0 0 24 24" aria-hidden="true">
          <rect x="2" y="5" width="20" height="14" fill="#f37021"/>
          <path d="M2 5l10 8 10-8" fill="none" stroke="#ffffff" stroke-width="1.6"/>
        </svg>
        <span>Tobias@hartuvo.nl</span>
      </li>
    </ul>

    <svg class="card-bands" width="615" height="350" viewBox="0 0 615 350" aria-hidden="true">
      <polygon points="0,338 341,338 330,350 0,350" fill="#111111"/>
      <polygon points="346,315 615,315 615,350 328,350" fill="#f37021"/>
    </svg>
    <span class="web-address">www.hartuvo.nl</span>
  </section>

  <section class="card card-back" aria-label="Business card back">
    <div class="wordmark back-wordmark">
      <span class="wordmark-dot" aria-hidden="true"></span>
      <span class="wordmark-name">hartuvo</span>
    </div>
    <p class="slogan">Because Quality Matters</p>
  </section>
</body>
</html>
```